Velk Partners Building Business Cards

We need a business card that reflects our business as "Solar Experts" in San Diego. Browse our website www.velkpartners.example our License needs to be displayed as "CSLB# 3867140" our phone number is (619) 555-0187

Save thousands on your electric bills and increase the value of your home while helping to protect the environment. Our solar installation experts will help you design the system that's right for you, using only the highest quality equipment that will look great and give you ideal performance. Our goal is to make you energy independent, and get your electric bill to 0.

Paul Osterby
(619) 555-0187
paul@velkpartners.example

Target Market(s)

Home owners in san diego looking for solar

Industry/Entity Type

Solar Energy

Contact Information for Business Card

Paul Osterby
(619) 555-0187
paul@velkpartners.example

Font styles to use
Other font styles liked:
• Use our logo font

Requirements
Must have
• License needs to be displayed as "CSLB# 3867140" our phone number is (619) 555-0187
Nice to have
• Real images of rooftop home solar in san diego
Should not have
• our business address

```html
<!DOCTYPE html>
<html lang="en">
<head>
<meta charset="utf-8">
<title>Velk Partners Building – Business Cards</title>
<link href="https://fonts.googleapis.com/css2?family=Open+Sans:wght@400;700&display=swap" rel="stylesheet">
<style>
  :root{
    --navy:#1d3f80;
    --navy-deep:#17356d;
    --sun:#f5a623;
    --paper:#ffffff;
    --stage:#ecebe8;
    --ink-soft:#e6ecf7;
  }
  *{box-sizing:border-box;margin:0;padding:0}
  html,body{width:1200px;height:950px;overflow:hidden}
  body{background:var(--stage);font-family:"Open Sans",Arial,sans-serif;position:relative}

  .card{position:absolute;left:250px;width:700px;height:400px;box-shadow:0 6px 18px rgba(0,0,0,.18);overflow:hidden}
  .card--front{top:60px;display:flex}
  .card--back{top:500px;background:var(--navy);display:flex;align-items:center;justify-content:center}

  .front__brand{width:300px;background:var(--paper);display:flex;align-items:center;justify-content:center}
  .front__details{position:relative;flex:1;background:var(--navy);border-left:5px solid var(--sun);padding:70px 0 0 70px;color:var(--paper)}
  .front__notch{position:absolute;left:-1px;top:74px;width:0;height:0;border-top:14px solid transparent;border-bottom:14px solid transparent;border-left:16px solid var(--sun)}

  .brand{display:flex;align-items:center;gap:12px;font-weight:700;line-height:1.05}
  .brand__dot{width:18px;height:18px;border-radius:50%;background:var(--sun);flex:none}
  .brand--light{color:var(--navy);font-size:30px}
  .brand--dark{color:var(--paper);font-size:46px}

  .person__name{color:var(--sun);font-weight:700;font-size:26px}
  .person__role{font-size:17px;margin-top:2px}
  .person__license{font-size:17px;margin-top:22px}
  .contact{list-style:none;margin-top:24px}
  .contact li{display:flex;align-items:center;gap:12px;font-size:17px;margin-bottom:8px}
  .contact svg{width:16px;height:16px;flex:none}
</style>
</head>
<body>
  <section class="card card--front" aria-label="Business card front">
    <div class="front__brand">
      <div class="brand brand--light"><span class="brand__dot"></span><span>Velk Partners<br>Building</span></div>
    </div>
    <div class="front__details">
      <span class="front__notch"></span>
      <p class="person__name">Paul Osterby</p>
      <p class="person__role">CEO/Founder</p>
      <p class="person__license">CSLB# 3867140</p>
      <ul class="contact">
        <li>
          <svg viewBox="0 0 16 16"><path fill="#f5a623" d="M3.5 1.5l2.5 3-1.5 1.8a9 9 0 0 0 5.2 5.2l1.8-1.5 3 2.5-1.6 2A12 12 0 0 1 1.5 3.1z"/></svg>
          (619) 555-0187
        </li>
        <li>
          <svg viewBox="0 0 16 16"><rect x="1" y="3" width="14" height="10" fill="#f5a623"/><path d="M1.5 3.5 8 9l6.5-5.5" stroke="#1d3f80" stroke-width="1.5" fill="none"/></svg>
          paul@velkpartners.example
        </li>
        <li>
          <svg viewBox="0 0 16 16"><circle cx="8" cy="8" r="7" fill="#f5a623"/><path d="M1 8h14M8 1c3 3 3 11 0 14M8 1c-3 3-3 11 0 14" stroke="#1d3f80" stroke-width="1.2" fill="none"/></svg>
          www.velkpartners.example
        </li>
      </ul>
    </div>
  </section>

  <section class="card card--back" aria-label="Business card back">
    <div class="brand brand--dark"><span class="brand__dot"></span><span>Velk Partners Building</span></div>
  </section>
</body>
</html>
```